Law Firm in Texas in need of new letterhead

Law Firm in Fort Worth, TX, USA named "Pell & Varnum, Attorneys-At-Law, LLP." This is a general practice law firm that mostly does Family Law and Criminal Defense work.

We are looking for a new letterhead that has a "classical" appeal, with modern elements.

Any color combination is fine, but please note that we do fax many documents, so the design must be clearly legible in Black and White.

We would like our letterhead to project a sense of professionalism, integrity, and ability.

Target Market(s)

Letterhead will be for correspondence generally with other attorneys and clients.

Industry/Entity Type

Law Firm

Logo Text

Pell & Varnum, Attorneys-At-Law, LLP.

Logo styles of interest
Pictorial/Combination Logo
Wordmark Logo
Lettermark Logo
Requirements
Nice to have
• Although not necessary, a "Texas Star" that is incorporated into the design would be a nice touch.
Should not have
• Colors that do not convert to B&W easily

```html
<!DOCTYPE html>
<html lang="en">
<head>
<meta charset="utf-8">
<title>Pell &amp; Varnum Letterhead</title>
<link rel="stylesheet" href="https://fonts.googleapis.com/css2?family=Archivo+Black&family=Archivo+Narrow:wght@700&display=swap">
<style>
  :root {
    --ink: #000000;
    --paper: #ffffff;
    --panel: #e6e6e6;
    --panel-edge: #f0f0f0;
  }
  html, body {
    margin: 0;
    padding: 0;
    overflow: hidden;
    background: var(--paper);
  }
  .letterhead {
    position: relative;
    width: 840px;
    height: 1200px;
    background: var(--paper);
    overflow: hidden;
    color: var(--ink);
  }
  .firm-mark {
    position: absolute;
    left: 18px;
    top: 62px;
    width: 140px;
    display: flex;
    align-items: center;
    gap: 8px;
  }
  .firm-mark__square {
    width: 14px;
    height: 14px;
    background: var(--ink);
    flex: none;
  }
  .firm-mark__name {
    font-family: "Archivo Black", sans-serif;
    font-size: 20px;
    line-height: 1.05;
  }
  .firm-title {
    position: absolute;
    left: 180px;
    top: 26px;
    margin: 0;
    font-family: "Archivo Narrow", sans-serif;
    font-weight: 700;
    font-size: 34px;
    line-height: 1;
    white-space: nowrap;
  }
  .title-rule {
    position: absolute;
    left: 172px;
    top: 58px;
    width: 650px;
    height: 12px;
  }
  .contact {
    position: absolute;
    left: 176px;
    top: 72px;
    margin: 0;
    font-family: "Archivo Black", sans-serif;
    font-size: 18px;
    line-height: 22.5px;
    letter-spacing: 1.6px;
    font-style: normal;
  }
  .contact__line { display: block; white-space: nowrap; }
  .contact__line--entity { letter-spacing: 1.9px; }
  .justice-art {
    position: absolute;
    left: 622px;
    top: 95px;
    width: 218px;
    height: 102px;
    background: linear-gradient(180deg, var(--panel-edge), var(--panel));
  }
</style>
</head>
<body>
  <div class="letterhead">
    <div class="firm-mark">
      <span class="firm-mark__square"></span>
      <span class="firm-mark__name">Pell &amp; Varnum</span>
    </div>

    <h1 class="firm-title">Pell &amp; Varnum, Attorneys-At-Law, LLP</h1>

    <svg class="title-rule" viewBox="0 0 650 12" aria-hidden="true">
      <line x1="0" y1="6" x2="640" y2="6" stroke="var(--ink)" stroke-width="2"/>
      <polyline points="632,1 646,6 632,11" fill="none" stroke="var(--ink)" stroke-width="2"/>
    </svg>

    <address class="contact">
      <span class="contact__line contact__line--entity">Pell &amp; Varnum, Attorneys-at-Law, LP</span>
      <span class="contact__line">1420 E. Harlan St.</span>
      <span class="contact__line">Fort Worth, TX 76104</span>
      <span class="contact__line">(817) 555-0142</span>
      <span class="contact__line">(817) 555-0198 (fax)</span>
    </address>

    <div class="justice-art" role="img" aria-label="Scales of justice illustration"></div>
  </div>
</body>
</html>
```